Online training business needs new website

We need a new wordpress website as a result of a rebranding. The business is a crisis management training company focussed on online training and simulation exercises. We only need a 4 page site - home, about us, contact us and blog. However we must be able to add additional tabs in the header to redirect to our sales and marketing system (Kartra). As these change from time to time, we must be able to add and delete as required.The site must be editable by us, with a basic understanding of wordpress and no understanding of coding. We don't want to have to employ someone to change text, add posts or add a new workshops etc. The theme chosen must be easy to edit by a beginner.

Target Market(s)

Senior managers food and consumer goods companies

Industry/Entity Type

Consulting

Coding

Coded - Design and coding required

Font styles to use
Sans Serif

Requirements
Must have
• Home page, about us, contact us, blog
• Colour scheme from logo (attached) - maroon, blue and grey
• If you go to the current website "tidewellcollege.com" and click on the "workshops" tab you will see the content I need on the home page for the plumvantage.com site
Nice to have
• Modern, simple and minimalist design is preferred

```html
<!DOCTYPE html>
<html lang="en">
<head>
<meta charset="utf-8">
<title>Plum Vantage — Blogs</title>
<link href="https://fonts.googleapis.com/css2?family=Roboto:wght@400;500;700&family=Open+Sans:wght@400;600;700&display=swap" rel="stylesheet">
<style>
:root{
  --maroon:#7d0f3f;
  --navy:#0b3868;
  --nav-blue:#1d4f8a;
  --ink:#333333;
  --muted:#555555;
  --line:#cfcfcf;
  --white:#ffffff;
  --read-green:#1f7a2a;
}
*{margin:0;padding:0;box-sizing:border-box}
html,body{width:1200px;height:2557px;overflow:hidden;background:var(--white)}
body{position:relative;font-family:"Open Sans",Arial,sans-serif;color:var(--ink)}
.abs{position:absolute}

/* header */
.site-header{position:absolute;left:0;top:0;width:1200px;height:113px;background:var(--white);z-index:3}
.brand{position:absolute;left:170px;top:0;width:165px;height:138px;border-radius:0 0 82px 82px;background:var(--white);display:flex;align-items:center;justify-content:center;z-index:4}
.brand-name{font-family:"Roboto",Arial,sans-serif;font-weight:700;font-size:25px;line-height:1.05;color:var(--maroon);text-align:center;text-transform:uppercase}
.main-nav{position:absolute;left:372px;top:49px;display:flex;gap:21px;font-family:"Roboto",Arial,sans-serif;font-size:17px;color:var(--nav-blue);text-transform:uppercase}
.main-nav .current{color:var(--maroon)}

/* hero */
.hero{position:absolute;left:0;top:113px;width:1200px;height:429px}
.hero-title{position:absolute;left:0;top:150px;width:1200px;text-align:center;font-family:"Roboto",Arial,sans-serif;font-weight:700;font-size:50px;color:var(--white);letter-spacing:1px;z-index:2}

/* section headings */
.section-title{position:absolute;left:0;width:1200px;text-align:center;font-family:"Roboto",Arial,sans-serif;font-weight:500;font-size:36px;text-transform:uppercase}
.section-title.maroon{color:var(--maroon)}
.section-title.light{color:var(--white);font-weight:400;font-size:31px}

/* recent blog cards */
.post-card{position:absolute;width:273px;height:312px;border:1px solid var(--line);background:var(--white);text-align:center}
.post-card .thumb{display:block;width:100%;height:178px}
.date-badge{position:absolute;left:76px;top:157px;width:115px;height:24px;background:var(--maroon);color:var(--white);font-family:"Roboto",Arial,sans-serif;font-size:14px;line-height:24px}
.post-card h3{font-family:"Roboto",Arial,sans-serif;font-weight:400;font-size:17px;color:var(--ink);margin-top:17px}
.post-card p{font-size:11px;line-height:16px;color:var(--muted);margin:8px 18px 0}
.read-more{display:block;margin-top:9px;font-size:11px;font-weight:700;color:var(--read-green);text-transform:uppercase}

/* audio */
.audio-card{position:absolute;width:205px;height:290px;background:var(--white);border:1px solid #d8d8d8;text-align:center}
.audio-card .thumb{display:block;width:100%;height:166px}
.audio-card h3{font-family:"Roboto",Arial,sans-serif;font-weight:400;font-size:16px;color:var(--ink);margin-top:14px}
.audio-card p{font-size:11.5px;line-height:16px;color:var(--muted);margin:8px 18px 0}
.listen{display:block;margin-top:4px;font-size:13px;font-weight:700;color:var(--maroon)}

/* video */
.video-card{position:absolute;width:405px;height:318px;border:1px solid var(--line);background:var(--white);text-align:center}
.video-card .thumb{display:block;width:100%;height:206px}
.play{position:absolute;left:170px;top:72px;width:62px;height:62px}
.video-card h3{font-family:"Roboto",Arial,sans-serif;font-weight:500;font-size:20px;color:var(--navy);margin-top:13px}
.video-card p{font-size:12px;line-height:18px;color:var(--muted);margin:6px 14px 0}

/* footer */
.site-footer{position:absolute;left:0;top:2410px;width:1200px;border-top:1px solid #bbbbbb;text-align:center}
.footer-nav{display:flex;justify-content:center;gap:22px;margin-top:40px;font-family:"Roboto",Arial,sans-serif;font-size:17px;color:var(--nav-blue);text-transform:uppercase}
.copyright{margin-top:14px;font-family:"Roboto",Arial,sans-serif;font-size:16px;color:#444}
</style>
</head>
<body>

<header class="site-header">
  <div class="brand"><span class="brand-name">Plum<br>Vantage</span></div>
  <nav class="main-nav">
    <span>About Us</span><span>Workshops</span><span>Online Course</span><span>Simulations</span><span>Contact Us</span><span class="current">Blog</span>
  </nav>
</header>

<section class="hero">
  <svg width="1200" height="429" viewBox="0 0 1200 429">
    <defs>
      <linearGradient id="heroShade" x1="0" y1="0" x2="1" y2="1">
        <stop offset="0" stop-color="#3b3a36"/>
        <stop offset="0.5" stop-color="#55595c"/>
        <stop offset="1" stop-color="#2c2d2f"/>
      </linearGradient>
    </defs>
    <rect width="1200" height="429" fill="url(#heroShade)" role="img" aria-label="Desk with a laptop showing a blog web page"/>
    <path d="M0 429 L0 420 Q600 300 1200 420 L1200 429 Z" fill="#ffffff"/>
    <path d="M110 410 Q600 320 1090 410" fill="none" stroke="#0b3868" stroke-width="7"/>
    <path d="M150 414 Q600 336 1050 414" fill="none" stroke="#7d0f3f" stroke-width="2"/>
    <circle cx="600" cy="360" r="36" fill="#ffffff"/>
  </svg>
  <h1 class="hero-title">BLOGS</h1>
</section>

<h2 class="section-title maroon" style="top:552px">Recent Blogs</h2>

<article class="post-card" style="left:162px;top:625px">
  <svg class="thumb" viewBox="0 0 273 178" preserveAspectRatio="none" role="img" aria-label="Business women meeting in an office"><rect width="273" height="178" fill="#b9a489"/></svg>
  <span class="date-badge">02 Aug 2017</span>
  <h3>Your Blog Title here</h3>
  <p>netus et malesuada fames ac turpis egestas Cras id elit Integer quis urna Ut ante enim dapibus malesuada fringilla eu cond</p>
  <span class="read-more">Read More</span>
</article>
<article class="post-card" style="left:456px;top:625px">
  <svg class="thumb" viewBox="0 0 273 178" preserveAspectRatio="none" role="img" aria-label="Hand drawing a financial line chart"><rect width="273" height="178" fill="#2e2e2e"/></svg>
  <span class="date-badge">02 Aug 2017</span>
  <h3>Your Blog Title here</h3>
  <p>netus et malesuada fames ac turpis egestas Cras id elit Integer quis urna Ut ante enim dapibus malesuada fringilla eu cond</p>
  <span class="read-more">Read More</span>
</article>
<article class="post-card" style="left:757px;top:625px">
  <svg class="thumb" viewBox="0 0 273 178" preserveAspectRatio="none" role="img" aria-label="Management team presentation in a meeting room"><rect width="273" height="178" fill="#c9c6c0"/></svg>
  <span class="date-badge">02 Aug 2017</span>
  <h3>Your Blog Title here</h3>
  <p>netus et malesuada fames ac turpis egestas Cras id elit Integer quis urna Ut ante enim dapibus malesuada fringilla eu cond</p>
  <span class="read-more">Read More</span>
</article>

<svg class="abs" style="left:0;top:1015px" width="1200" height="560" viewBox="0 0 1200 560">
  <path d="M0 80 Q600 -30 1200 35 L1200 120 L0 120 Z" fill="#7d0f3f"/>
  <path d="M0 98 Q600 -12 1200 50 L1200 470 Q600 580 0 475 Z" fill="#0b3868"/>
  <path d="M500 540 Q900 545 1200 477 L1200 495 Q900 560 500 540 Z" fill="#7d0f3f"/>
</svg>

<h2 class="section-title light" style="top:1095px">Audio Blogs</h2>

<article class="audio-card" style="left:162px;top:1168px">
  <svg class="thumb" viewBox="0 0 205 166" preserveAspectRatio="none" role="img" aria-label="Blue sound wave on a dark background"><defs><linearGradient id="wave" x1="0" y1="0" x2="0" y2="1"><stop offset="0" stop-color="#0a1230"/><stop offset="0.5" stop-color="#1f5fa8"/><stop offset="1" stop-color="#0a1230"/></linearGradient></defs><rect width="205" height="166" fill="url(#wave)"/></svg>
  <h3>Your Blog Title here</h3>
  <p>Aetus et malesuada fames ac turpis egestas Cras id elit</p>
  <span class="listen">Listen Now</span>
</article>
<article class="audio-card" style="left:382px;top:1168px">
  <svg class="thumb" viewBox="0 0 205 166" preserveAspectRatio="none" role="img" aria-label="Blue sound wave on a dark background"><rect width="205" height="166" fill="url(#wave)"/></svg>
  <h3>Your Blog Title here</h3>
  <p>Aetus et malesuada fames ac turpis egestas Cras id elit</p>
  <span class="listen">Listen Now</span>
</article>
<article class="audio-card" style="left:602px;top:1168px">
  <svg class="thumb" viewBox="0 0 205 166" preserveAspectRatio="none" role="img" aria-label="Blue sound wave on a dark background"><rect width="205" height="166" fill="url(#wave)"/></svg>
  <h3>Your Blog Title here</h3>
  <p>Aetus et malesuada fames ac turpis egestas Cras id elit</p>
  <span class="listen">Listen Now</span>
</article>
<article class="audio-card" style="left:822px;top:1168px">
  <svg class="thumb" viewBox="0 0 205 166" preserveAspectRatio="none" role="img" aria-label="Blue sound wave on a dark background"><rect width="205" height="166" fill="url(#wave)"/></svg>
  <h3>Your Blog Title here</h3>
  <p>Aetus et malesuada fames ac turpis egestas Cras id elit</p>
  <span class="listen">Listen Now</span>
</article>

<h2 class="section-title maroon" style="top:1624px">Video Blogs</h2>

<article class="video-card" style="left:186px;top:1695px">
  <svg class="thumb" viewBox="0 0 405 206" preserveAspectRatio="none" role="img" aria-label="Businessman working at a laptop with charts"><rect width="405" height="206" fill="#9a9c9f"/></svg>
  <svg class="play" viewBox="0 0 62 62"><circle cx="31" cy="31" r="31" fill="#fff"/><path d="M24 18 L45 31 L24 44 Z" fill="#111"/></svg>
  <h3>Video Blog Title here</h3>
  <p>Morbi diam mauris viverra in gravida eu mattis in ante Morbi eget arcu Morbi porta libero id ullamcorper nonummy</p>
</article>
<article class="video-card" style="left:614px;top:1695px">
  <svg class="thumb" viewBox="0 0 405 206" preserveAspectRatio="none" role="img" aria-label="Man in glasses working in a bright office"><rect width="405" height="206" fill="#7e8f9e"/></svg>
  <svg class="play" viewBox="0 0 62 62"><circle cx="31" cy="31" r="31" fill="#fff"/><path d="M24 18 L45 31 L24 44 Z" fill="#111"/></svg>
  <h3>Video Blog Title here</h3>
  <p>Morbi diam mauris viverra in gravida eu mattis in ante Morbi eget arcu Morbi porta libero id ullamcorper nonummy</p>
</article>
<article class="video-card" style="left:191px;top:2031px">
  <svg class="thumb" viewBox="0 0 405 206" preserveAspectRatio="none" role="img" aria-label="Businessmen holding black umbrellas in the rain"><rect width="405" height="206" fill="#4d5a63"/></svg>
  <svg class="play" viewBox="0 0 62 62"><circle cx="31" cy="31" r="31" fill="#fff"/><path d="M24 18 L45 31 L24 44 Z" fill="#111"/></svg>
  <h3>Video Blog Title here</h3>
  <p>Morbi diam mauris viverra in gravida eu mattis in ante Morbi eget arcu Morbi porta libero id ullamcorper nonummy</p>
</article>
<article class="video-card" style="left:619px;top:2031px">
  <svg class="thumb" viewBox="0 0 405 206" preserveAspectRatio="none" role="img" aria-label="Stressed man looking at a computer screen"><rect width="405" height="206" fill="#b7b4ad"/></svg>
  <svg class="play" viewBox="0 0 62 62"><circle cx="31" cy="31" r="31" fill="#fff"/><path d="M24 18 L45 31 L24 44 Z" fill="#111"/></svg>
  <h3>Video Blog Title here</h3>
  <p>Morbi diam mauris viverra in gravida eu mattis in ante Morbi eget arcu Morbi porta libero id ullamcorper nonummy</p>
</article>

<footer class="site-footer">
  <nav class="footer-nav">
    <span>About Us</span><span>Workshops</span><span>Online Course</span><span>Simulations</span><span>Contact Us</span><span>Blog</span>
  </nav>
  <p class="copyright">© 2019 Company Name &nbsp;All right reserved</p>
</footer>

</body>
</html>
```